Black Car Limousine transportation business in Naples Florida

Always stand for my reliability and RVD stands for Love, K and M are the first initials of my children's names. It should show professionalism and a dedication to customer service. We keep our clients identities private. Show our professionalism. We are Black car Black tie company. We service transportation on a reserve basis to and from residents, airports, casinos, hotels,

Target Market(s)

It is a Private car service. High end clients. Businesses, Celebrity and athletes. Service to airports, hotels, special events.

Industry/Entity Type

Business

Contact Information for Business Card

A pearl metallic or Luster card. Standard business card size. Would like the name, Company email, show we take credit cards and phone number. Currently I don't have a website but will like to add later.

Logo Text

STEADFAST RVD TRANSPORTATION

Font styles to use
Serif

Colors
eaeaea
000000

Requirements
Must have
• Must have Company email, show we take credit cards and phone number. Currently I don't have a website but will like to add later.
Nice to have
• Would like to stay with a black and white theme. Open to some color trim.
Should not have
• Open to suggestions

```html
<!DOCTYPE html>
<html lang="en">
<head>
<meta charset="utf-8">
<title>Steadfast RVD Transportation – Business Card</title>
<link href="https://fonts.googleapis.com/css2?family=Lora:wght@400;600;700&display=swap" rel="stylesheet">
<style>
  :root {
    --stage: #e4e2df;
    --card-white: #ffffff;
    --card-dark: #333333;
    --ink: #222222;
    --ink-soft: #333333;
    --paper-text: #ffffff;
    --photo-dark: #1a1a1a;
    --photo-mid: #4a4a4a;
    --card-icon: #eaeaea;
  }
  html, body {
    margin: 0;
    padding: 0;
    width: 1200px;
    height: 900px;
    overflow: hidden;
    background: var(--stage);
    font-family: "Lora", Georgia, serif;
  }
  .canvas {
    position: relative;
    width: 1200px;
    height: 900px;
  }
  .card {
    position: absolute;
    box-shadow: 0 4px 14px rgba(0,0,0,0.18);
  }
  .card-front {
    left: 78px;
    top: 34px;
    width: 588px;
    height: 363px;
    background: var(--card-white);
    color: var(--ink);
  }
  .card-back {
    left: 388px;
    top: 505px;
    width: 566px;
    height: 351px;
    background: var(--card-dark);
    color: var(--paper-text);
  }
  .wordmark {
    position: absolute;
    text-align: center;
    font-weight: 700;
    line-height: 1;
    letter-spacing: 0.5px;
  }
  .wordmark .name-main { display: block; }
  .wordmark .name-sub { display: block; letter-spacing: 1px; }
  .card-front .wordmark {
    left: 0;
    width: 588px;
    top: 48px;
    color: var(--ink);
  }
  .card-front .name-main { font-size: 42px; }
  .card-front .name-sub { font-size: 23px; margin-top: 10px; }
  .card-back .wordmark {
    left: 0;
    width: 566px;
    top: 118px;
    color: var(--paper-text);
  }
  .card-back .name-main { font-size: 48px; }
  .card-back .name-sub { font-size: 28px; margin-top: 12px; }

  .contact {
    position: absolute;
    left: 35px;
    top: 163px;
    color: var(--ink-soft);
  }
  .person-name {
    font-size: 20px;
    font-weight: 700;
    margin: 0;
    line-height: 26px;
  }
  .person-role {
    font-size: 15px;
    margin: 0 0 7px 0;
    line-height: 19px;
  }
  .contact-line {
    display: flex;
    align-items: center;
    gap: 8px;
    font-size: 15px;
    line-height: 23px;
  }
  .contact-line svg { width: 13px; height: 13px; fill: var(--ink-soft); }
  .address {
    font-size: 15px;
    line-height: 21px;
    margin-top: 5px;
  }
  .vehicle-photo {
    position: absolute;
    left: 272px;
    top: 152px;
    width: 282px;
    height: 158px;
    border-radius: 24px 40px 14px 14px;
    background: linear-gradient(160deg, var(--photo-mid), var(--photo-dark) 60%);
  }
  .web-band {
    position: absolute;
    left: 0;
    bottom: 0;
    width: 100%;
    height: 49px;
    background: var(--card-dark);
    color: var(--paper-text);
    font-size: 15px;
    display: flex;
    align-items: center;
    justify-content: center;
  }
  .cards-accepted {
    position: absolute;
    right: 18px;
    top: 50%;
    transform: translateY(-50%);
    display: flex;
    gap: 6px;
  }
  .cards-accepted svg { width: 30px; height: 20px; }
</style>
</head>
<body>
<main class="canvas">
  <section class="card card-front" aria-label="Business card front">
    <div class="wordmark">
      <span class="name-main">STEADFAST RVD</span>
      <span class="name-sub">TRANSPORTATION</span>
    </div>
    <div class="contact">
      <p class="person-name">Daniel Harper</p>
      <p class="person-role">Managing Director</p>
      <div class="contact-line">
        <svg viewBox="0 0 16 16" aria-hidden="true"><path d="M1 5c0-2 3-3 7-3s7 1 7 3v1h-4V5H5v1H1zM4 7h8l3 3v4H1v-4zm4 1.5a2 2 0 100 4 2 2 0 000-4z"/></svg>
        <span>044-987 654 321</span>
      </div>
      <div class="contact-line">
        <svg viewBox="0 0 16 16" aria-hidden="true"><path d="M1 3h14v10H1zm1.5 1.5v.4L8 9l5.5-4.1v-.4zm0 2.2v4.8h11V6.7L8 10.8z"/></svg>
        <span>info@mailsample.com</span>
      </div>
      <div class="address">67890, Harbor Lane Road<br>Country Name, 123456.</div>
    </div>
    <div class="vehicle-photo" role="img" aria-label="Photo of a black luxury SUV"></div>
    <div class="web-band">
      <span>www.sitesample.com</span>
      <div class="cards-accepted" role="img" aria-label="Credit cards accepted">
        <svg viewBox="0 0 30 20" aria-hidden="true"><rect x="0.5" y="0.5" width="29" height="19" rx="3" fill="none" stroke="var(--card-icon)"/><rect x="0.5" y="5" width="29" height="3.5" fill="var(--card-icon)"/><rect x="4" y="12.5" width="9" height="2.5" fill="var(--card-icon)"/></svg>
        <svg viewBox="0 0 30 20" aria-hidden="true"><rect x="0.5" y="0.5" width="29" height="19" rx="3" fill="none" stroke="var(--card-icon)"/><rect x="4" y="5" width="6" height="5" rx="1" fill="var(--card-icon)"/><rect x="4" y="13" width="16" height="2.5" fill="var(--card-icon)"/></svg>
      </div>
    </div>
  </section>

  <section class="card card-back" aria-label="Business card back">
    <div class="wordmark">
      <span class="name-main">STEADFAST RVD</span>
      <span class="name-sub">TRANSPORTATION</span>
    </div>
  </section>
</main>
</body>
</html>
```